Website Redesign Project Puzzle Vault Larkfield

We are an escape room company located in Ashburn, Virginia. We currently have a website https://www.puzzlevaultlarkfield.example based upon html/bootstrap/javascript/php/mysql and I'd like to keep it that way. I'm looking for someone upgrade the front page so it is more informative, cleaner, quicker to load, and optimizes the space for full sale opportunities.

Target Market(s)

Corporate Clients, Families, Friends. All ages

Industry/Entity Type

Entertainment Industry

Coding

Coded - Design and coding required

Number of Pages Required

3 page

Font styles to use
Other font styles liked:
• Similar to Facebook or Amazon

Requirements
Must have
• Must be mobile friendly. bootstrap. Lots of graphics (will provide) nice and easy to read fonts. Easy to read layout. Must look clean, fresh, exciting, and want to grab attention.
• Please visit my facebook page and website for more details. facebook.com/puzzlevaultlarkfield
Nice to have
• Same color as existing but open to options if they look nice.
Should not have
• Should not be wordpress or hard to modify.

```html
<!DOCTYPE html>
<html lang="en">
<head>
<meta charset="utf-8">
<title>Puzzle Vault Larkfield</title>
<link rel="stylesheet" href="https://fonts.googleapis.com/css2?family=Open+Sans:wght@400;600;700&display=swap">
<style>
:root{
  --blue:#0ea2e6;
  --title:#1b9ddc;
  --ink:#222;
  --muted:#555;
  --pale:#eef0f3;
  --field:#f0f1f3;
  --line:#dcdfe3;
  --black:#000;
  --white:#fff;
  --hero-a:#2b2fa8;
  --hero-b:#6a1fa3;
}
*{box-sizing:border-box;margin:0;padding:0}
html,body{width:1200px;height:3701px;overflow:hidden}
body{font-family:"Open Sans",Arial,sans-serif;color:var(--ink);background:var(--white)}
.wrap{width:900px;margin:0 auto;position:relative}
.btn{display:inline-block;background:var(--blue);color:var(--white);font-weight:700;font-size:12px;text-transform:uppercase;text-decoration:none;border-radius:3px;text-align:center}
.section-title{color:var(--title);font-size:23px;font-weight:600;text-align:center;text-transform:uppercase;letter-spacing:.3px}

/* nav */
.topbar{height:86px;background:var(--black)}
.topbar .wrap{display:flex;align-items:center;height:86px}
.brand{display:flex;align-items:center;gap:8px;color:var(--blue);font-weight:700;font-size:17px;line-height:1.05;width:140px}
.brand-mark{width:16px;height:16px;background:var(--blue);flex:none}
.menu{display:flex;gap:38px;margin-left:8px;list-style:none}
.menu a{color:var(--white);font-size:13.5px;font-weight:600;text-decoration:none}
.menu a.active{color:var(--blue)}
.topbar .btn{margin-left:auto;padding:9px 16px;font-size:13px}

/* hero */
.hero{height:419px;background:linear-gradient(100deg,var(--hero-a),var(--hero-b));color:var(--white);position:relative}
.hero-copy{position:absolute;left:150px;top:72px;width:590px;text-align:center}
.hero-copy .welcome{font-size:27px}
.hero-copy h1{font-size:46px;font-weight:400;letter-spacing:1.5px;margin-top:10px}
.hero-copy p{font-size:18px;line-height:23px;margin-top:18px}
.hero-copy .btn{margin-top:36px;padding:14px 27px;font-size:13.5px}
.hero-art{position:absolute;left:780px;top:40px;width:270px;height:340px;border-radius:40%;background:radial-gradient(circle,#4d5fd6,rgba(80,60,180,0) 70%)}

/* rooms */
.rooms{height:1060px;background:var(--pale);padding-top:34px}
.room-grid{display:grid;grid-template-columns:repeat(3,285px);column-gap:22px;row-gap:24px;margin-top:26px}
.room{background:var(--white);height:446px;border:1px solid var(--line);text-align:center;position:relative}
.room-photo{height:225px}
.room h3{font-size:17px;font-weight:600;margin-top:19px;letter-spacing:.3px}
.room p{font-size:10.5px;line-height:18px;color:var(--muted);font-weight:600;padding:0 20px;margin-top:12px}
.room .price{position:absolute;top:356px;left:0;right:0;font-size:13px;color:var(--muted);word-spacing:2px}
.room .btn{position:absolute;top:390px;left:91px;width:102px;padding:10px 0;font-size:11px}

/* events */
.events{height:762px;padding-top:45px}
.events .lead{text-align:center;font-size:13px;line-height:23px;color:#444;margin-top:16px}
.event-row{display:flex;justify-content:space-between;margin-top:47px}
.event{width:163px;text-align:center}
.event-ring{width:163px;height:163px;border:3px solid var(--blue);border-radius:50%;display:flex;align-items:center;justify-content:center}
.event h4{font-size:12.5px;font-weight:700;margin-top:22px}
.form{display:flex;justify-content:space-between;margin-top:37px}
.form .col{width:441px}
.field{display:block;width:100%;height:37px;background:var(--field);border:1px solid var(--line);font-size:12px;color:#888;padding:10px 14px;margin-bottom:8px}
.area{height:217px}
.form-submit{text-align:center;margin-top:24px}
.form-submit .btn{padding:10px 22px;font-size:11px}

/* faq */
.faq{height:561px;background:var(--pale);padding-top:33px}
.faq-grid{display:grid;grid-template-columns:288px 288px 290px;column-gap:16px;row-gap:15px;margin-top:24px}
.faq-card{background:var(--white);height:135px;text-align:center;padding:10px 10px}
.faq-card.last{height:118px}
.faq-card h4{font-size:14.5px;font-weight:600}
.faq-card p{font-size:10.5px;line-height:18px;color:#444;margin-top:5px}
.faq-card a{color:var(--blue);font-weight:700;text-decoration:none}

/* location */
.location{height:412px;padding-top:33px}
.loc-body{display:flex;margin-top:22px}
.map{width:442px;height:267px;background:linear-gradient(135deg,#eceef0,#dfe4e6 60%,#c8e2b6)}
.loc-info{flex:1;text-align:center;padding-top:26px;padding-left:20px}
.loc-info h5{font-size:14px;font-weight:600;margin-top:18px}
.loc-info h5:first-child{margin-top:0}
.loc-info p{font-size:14px;line-height:27px;color:#333}

/* contact */
.contact{height:401px;background:var(--pale);padding-top:33px;position:relative}
.contact .sub{text-align:center;font-size:13px;color:#444;margin-top:13px}
.contact .sub b{font-weight:600;color:var(--ink)}
.contact .form{margin-top:20px}
.contact .field{background:var(--white);height:35px;margin-bottom:9px}
.contact .area{height:123px}
.contact .form-submit{margin-top:24px}
.footer{position:absolute;left:150px;right:150px;top:372px;display:flex;align-items:center;justify-content:space-between;font-size:9px;color:#444}
.social{display:flex;gap:5px}
.social span{width:19px;height:19px;border-radius:50%;background:var(--blue)}
</style>
</head>
<body>

<header class="topbar">
  <div class="wrap">
    <div class="brand"><span class="brand-mark"></span>Puzzle Vault Larkfield</div>
    <ul class="menu">
      <li><a class="active" href="#rooms">ESCAPE ROOMS</a></li>
      <li><a href="#events">SPECIAL EVENTS</a></li>
      <li><a href="#how">HOW IT WORKS</a></li>
      <li><a href="#location">LOCATION</a></li>
      <li><a href="#contact">CONTACT US</a></li>
    </ul>
    <a class="btn" href="#rooms">BOOK NOW</a>
  </div>
</header>

<section class="hero">
  <div class="hero-copy">
    <div class="welcome">Welcome to</div>
    <h1>LARKFIELD PUZZLE VAULT</h1>
    <p>Experience this hour-long exciting &amp; thrilling entertainment! Cracking codes, discovering clues, and solving puzzles, you will find your ingenuity. Bring your friend and family together, and enjoy the adventure.</p>
    <a class="btn" href="#rooms">BOOK NOW</a>
  </div>
  <div class="hero-art" role="img" aria-label="Cartoon detective mascot holding a magnifying glass"></div>
</section>

<section class="rooms" id="rooms">
  <div class="wrap">
    <h2 class="section-title">Choose your own escape room</h2>
    <div class="room-grid">
      <article class="room">
        <div class="room-photo" role="img" aria-label="Group of players inside the red-lit elevator room" style="background:linear-gradient(160deg,#3a1a3c,#b0324a 60%,#2a1420)"></div>
        <h3>ELEVATOR</h3>
        <p>The main elevators are down so you'll need to take the freight elevator to the top floor if you want to get your award. The last celebrity that attempted to do so wasn't so lucky.</p>
        <div class="price">$28.00/person. &nbsp;&nbsp;&nbsp;Min: 4 Max: 6</div>
        <a class="btn" href="#">BOOK NOW</a>
      </article>
      <article class="room">
        <div class="room-photo" role="img" aria-label="Presidential seal behind a gold microphone" style="background:linear-gradient(135deg,#1d2a55,#c8a040 55%,#b33a3a)"></div>
        <h3>THE SPEECH</h3>
        <p>The President's speech has been hijacked and replaced with lyrics from an 80s hit song. Your task is to go in and find the correct speech before he takes the podium.</p>
        <div class="price">$28.00/person. &nbsp;&nbsp;&nbsp;Min: 4 Max: 8</div>
        <a class="btn" href="#">BOOK NOW</a>
      </article>
      <article class="room">
        <div class="room-photo" role="img" aria-label="Heavy bank vault door" style="background:linear-gradient(135deg,#6c6a86,#a9a6c2 50%,#4c4a62)"></div>
        <h3>BANK HEIST</h3>
        <p>With your family held hostage, the mob gave you one choice - rob the bank in exchange for their freedom or its goodbyes forever.</p>
        <div class="price">$28.00/person. &nbsp;&nbsp;&nbsp;Min:2 Max: 8</div>
        <a class="btn" href="#">BOOK NOW</a>
      </article>
      <article class="room">
        <div class="room-photo" role="img" aria-label="Players in orange jumpsuits in the jail room" style="background:linear-gradient(160deg,#3a3d40,#d0602e 60%,#5a4a44)"></div>
        <h3>JAIL BREAK</h3>
        <p>One Guard, One Goal: get out.</p>
        <div class="price">$28.00/person. &nbsp;&nbsp;&nbsp;Min: 2 Max: 6</div>
        <a class="btn" href="#">BOOK NOW</a>
      </article>
      <article class="room">
        <div class="room-photo" role="img" aria-label="Candy shop room with striped walls and candy tubes" style="background:linear-gradient(90deg,#b9c6de,#e8e6d8 50%,#c64a5a)"></div>
        <h3>CANDY SHOP</h3>
        <p>With all of the candy right before your eyes, find the golden ticket and win the prize!</p>
        <div class="price">$28.00/person. &nbsp;&nbsp;&nbsp;Min: 2 Max: 8</div>
        <a class="btn" href="#">BOOK NOW</a>
      </article>
      <article class="room">
        <div class="room-photo" role="img" aria-label="Large group of happy players in the lobby" style="background:linear-gradient(160deg,#2a3440,#8a8a86 55%,#c9b7a0)"></div>
        <h3>MORE TO COME</h3>
        <p>Visit our website regularly because we'll update our rooms in the future. Now, just try one of our adventureful rooms.</p>
        <a class="btn" href="#">BOOK NOW</a>
      </article>
    </div>
  </div>
</section>

<section class="events" id="events">
  <div class="wrap">
    <h2 class="section-title">Special events</h2>
    <p class="lead">Puzzle Vault Larkfield is the perfect place to gather groups of colleagues, friends, or family and experience the latest entertainment in town. Simply complete the form below and our specialist will contact you for further details. Group pricing is available on group parties.</p>
    <div class="event-row">
      <div class="event">
        <div class="event-ring">
          <svg width="76" height="68" viewBox="0 0 76 68" aria-hidden="true"><path d="M38 66 C10 44 2 32 2 20 C2 9 11 2 20 2 C28 2 34 7 38 13 C42 7 48 2 56 2 C65 2 74 9 74 20 C74 32 66 44 38 66Z" fill="#e4323f"/></svg>
        </div>
        <h4>CORPORATE MEETINGS</h4>
      </div>
      <div class="event">
        <div class="event-ring">
          <svg width="90" height="80" viewBox="0 0 90 80" aria-hidden="true"><rect x="35" y="4" width="3" height="18" fill="#f4c542"/><rect x="50" y="4" width="3" height="18" fill="#6cc4e8"/><rect x="14" y="22" width="62" height="22" rx="4" fill="#f49ac1"/><rect x="6" y="44" width="78" height="28" rx="4" fill="#ee6aa0"/><rect x="2" y="72" width="86" height="5" rx="2" fill="#8fd1ea"/></svg>
        </div>
        <h4>BIRTHDAY PARTIES</h4>
      </div>
      <div class="event">
        <div class="event-ring">
          <svg width="84" height="110" viewBox="0 0 84 110" aria-hidden="true"><ellipse cx="54" cy="24" rx="18" ry="22" fill="#f5e12a"/><ellipse cx="22" cy="44" rx="17" ry="21" fill="#5ac3d9"/><ellipse cx="56" cy="54" rx="17" ry="21" fill="#e8338a"/><path d="M22 65 Q30 90 40 105 M56 75 Q48 92 40 105 M54 46 Q46 80 40 105" stroke="#888" fill="none"/></svg>
        </div>
        <h4>ANNIVERSARIES</h4>
      </div>
      <div class="event">
        <div class="event-ring">
          <svg width="76" height="90" viewBox="0 0 76 90" aria-hidden="true"><path d="M48 10 L72 82 L4 70Z" fill="#e84430"/><path d="M4 70 L72 82" stroke="#f4b92e" stroke-width="6"/><circle cx="48" cy="8" r="6" fill="#f4b92e"/></svg>
        </div>
        <h4>HOLIDAYS</h4>
      </div>
    </div>
    <form class="form">
      <div class="col">
        <span class="field">Your Name *</span>
        <span class="field">Company Name</span>
        <span class="field">Your Email *</span>
        <span class="field">Size of Party</span>
        <span class="field">Your Phone *</span>
      </div>
      <div class="col"><span class="field area">Your Message *</span></div>
    </form>
    <div class="form-submit"><a class="btn" href="#">SEND MESSAGE</a></div>
  </div>
</section>

<section class="faq" id="how">
  <div class="wrap">
    <h2 class="section-title">How it works</h2>
    <div class="faq-grid">
      <div class="faq-card"><h4>How do I make a reservation?</h4><p>Click on the Book now button or click here.<br><a href="#">Book Now</a></p></div>
      <div class="faq-card"><h4>How long does an escape last?</h4><p>Each escape lasts 60 minutes.</p></div>
      <div class="faq-card"><h4>Is there an age limit?</h4><p>Participants 12 and older can be by themselves as long as an adult signs the waivers and is available for emergencies. Participants under 12 must be accompanied by an adult in the room or at the facility.</p></div>
      <div class="faq-card"><h4>I'm pregnant, can I participate?</h4><p>Less than 8 months yes.</p></div>
      <div class="faq-card"><h4>How can I redeem a voucher or promo code?</h4><p>Click on the Book Now button and enter the code in the promo code text box.</p></div>
      <div class="faq-card"><h4>Where do I park?</h4><p>Plenty of parking in front of the building</p></div>
      <div class="faq-card last"><h4>Do I have to sign a liability waiver?</h4><p>Yes. You can find the liability waiver here.<br><a href="#">Click here for waiver</a></p></div>
      <div class="faq-card last"><h4>Which room is the most challenging?</h4><p>They are all challenging!</p></div>
      <div class="faq-card last"><h4>What is the cancellation policy?</h4><p>24 hours notice from the scheduled reservation date. If you don't cancel within 24 hours you will lose your reservation and payment.</p></div>
    </div>
  </div>
</section>

<section class="location" id="location">
  <div class="wrap">
    <h2 class="section-title">Location</h2>
    <div class="loc-body">
      <div class="map" role="img" aria-label="Street map showing the venue location"></div>
      <div class="loc-info">
        <h5>ADDRESS</h5>
        <p>1180 Maple Hollow Drive, Suite 205 Larkfield, VA 20100</p>
        <h5>PHONE NUMBER</h5>
        <p>(555) 014 2606</p>
        <h5>HOURS</h5>
        <p>Wednesday - Friday : 4pm - 10pm<br>Saturday : 11am - 11pm<br>Sunday : 11am - 9:30pm.</p>
      </div>
    </div>
  </div>
</section>

<section class="contact" id="contact">
  <div class="wrap">
    <h2 class="section-title">Contact us</h2>
    <p class="sub">Call <b>555 014 2606</b> &nbsp;or &nbsp;Send Us a Message.</p>
    <form class="form">
      <div class="col">
        <span class="field">Your Name</span>
        <span class="field">Your Email</span>
        <span class="field">Your Phone</span>
      </div>
      <div class="col"><span class="field area">We'd love to hear from you. We'll get back to you immediately.</span></div>
    </form>
    <div class="form-submit"><a class="btn" href="#">SUBMIT</a></div>
  </div>
  <footer class="footer">
    <span>Copyright @ Puzzle Vault Larkfield</span>
    <div class="social"><span></span><span></span><span></span><span></span></div>
  </footer>
</section>

</body>
</html>
```